BRV Early College and Career Program

Starting a new program initiative at Birchmont Valley School where students will have the opportunity to take college courses during their senior year of high school. Preferably add some pictures to reflect the career pathways we are offering (below) Some context to use for this flyer are:

Learn more about the career focused courses in…
• Education
• Computer & Information Science
• Technology & Engineering
• Health

Things to look forward to:
Experience college in high school
Finish college early
Save money on college tuition and fees
Advice on Career pathways

all classes fit into OPAL CREDIT BUNDLE

For more information contact

Gavin Purdy - ZT12 Alliances -WHVC
555.014.2291
Email: gpurdy@whvc-example.edu

Ms. Okafuji- Early College Coordinator
Email: dena.okafuji@birchmont-example.org
Room J215

I uploaded 5 or so photos that I would like to see incorporated in the design of the flier- using real students from our high school will give a more realistic approach- thanks, Added Monday, August 21, 2017

Target Market(s)

High school students who are currently in 10th grade (for recruitment) and only high school juniors and seniors are able to apply.

Industry/Entity Type

School

Colors

Designer to choose colors to be used in the design.

Requirements
Must have
• logos- some pictures reflecting the different career pathways and the contact information provided. Looking to also have this in a format that I can print on card stock paper not just full length page- ADD / USE photos attached to see which one fits the project better.
Nice to have
• suitable for high school students- attractive
Should not have
• Do not include any generic phone numbers.

```html
<!DOCTYPE html>
<html lang="en">
<head>
<meta charset="utf-8">
<title>BRV Early College Program</title>
<link href="https://fonts.googleapis.com/css2?family=Open+Sans:wght@400;600&family=Source+Sans+3:wght@400;600&display=swap" rel="stylesheet">
<style>
  :root {
    --navy: #173864;
    --blue: #3f78c6;
    --sky: #5b92d6;
    --ring: #cfd3d8;
    --ink: #1d3c6c;
    --grey-text: #555b63;
    --paper: #ffffff;
  }
  * { margin: 0; padding: 0; box-sizing: border-box; }
  html, body { width: 926px; height: 1200px; overflow: hidden; background: var(--paper); }
  body { font-family: "Source Sans 3", "Open Sans", sans-serif; }
  .flyer { position: relative; width: 926px; height: 1200px; }
  .backdrop { position: absolute; inset: 0; }
  .abs { position: absolute; }

  .brand { display: flex; align-items: center; gap: 8px; color: var(--navy); font-weight: 600; font-size: 19px; line-height: 1.05; }
  .brand-mark { width: 16px; height: 16px; background: var(--navy); flex: none; }
  .brand-mark.round { border-radius: 50%; background: var(--blue); }
  .brand-school { left: 455px; top: 152px; width: 210px; }
  .brand-college { left: 690px; top: 152px; width: 220px; }

  .program-title { left: 480px; top: 228px; width: 410px; text-align: center; color: #fff;
    font-family: "Open Sans", sans-serif; font-weight: 600; font-size: 35px; line-height: 48px; }
  .program-lede { left: 630px; top: 372px; width: 380px; transform: translateX(-50%); margin-left: 98px;
    text-align: center; color: var(--ink); font-weight: 600; font-size: 22px; line-height: 27.5px; }

  .perks { left: 34px; top: 525px; }
  .perks-heading { color: var(--ink); font-weight: 600; font-size: 18.5px; margin-bottom: 4px; }
  .perks-list { list-style: none; }
  .perks-list li { display: flex; align-items: center; gap: 9px; color: var(--grey-text);
    font-size: 19.5px; height: 28.8px; }
  .perks-list svg { flex: none; }

  .pathway-label { color: #fff; font-family: "Open Sans", sans-serif; font-size: 18px; font-weight: 400;
    text-align: center; line-height: 25px; width: 260px; transform: translateX(-50%); }

  .contact-banner { left: 517px; top: 904px; width: 409px; height: 47px; background: var(--sky);
    clip-path: polygon(16px 0, 100% 0, 100% 100%, 0 100%); color: #fff;
    font-family: "Open Sans", sans-serif; font-size: 18.5px; display: flex; align-items: center; padding-left: 46px; }

  .contact { top: 1018px; color: #d7e2f1; }
  .contact-name { color: #fff; font-weight: 600; font-size: 21px; margin-bottom: 2px; }
  .contact-line { font-size: 17.5px; line-height: 25px; }
  .contact-mail { display: flex; align-items: center; gap: 7px; font-size: 17px; letter-spacing: -0.2px; }
</style>
</head>
<body>
<main class="flyer">
  <svg class="backdrop" width="926" height="1200" viewBox="0 0 926 1200" xmlns="http://www.w3.org/2000/svg">
    <defs>
      <linearGradient id="photoTone" x1="0" y1="0" x2="1" y2="1">
        <stop offset="0" stop-color="#c9b9a5"/>
        <stop offset="0.5" stop-color="#b3a796"/>
        <stop offset="1" stop-color="#d7d0c4"/>
      </linearGradient>
      <linearGradient id="disc" x1="0" y1="0" x2="0" y2="1">
        <stop offset="0" stop-color="#6a9fe0"/>
        <stop offset="0.5" stop-color="#4c86d2"/>
        <stop offset="1" stop-color="#3f78c6"/>
      </linearGradient>
    </defs>

    <polygon role="img" aria-label="Photo of two students sitting on school steps reading a textbook together"
      points="0,0 275,0 585,502 0,502" fill="url(#photoTone)"/>
    <polygon points="275,0 297,0 607,502 585,502" fill="var(--blue)"/>
    <polygon points="297,0 304,0 614,502 607,502" fill="#cfd6df"/>

    <polygon points="436,192 926,192 926,196 438,196" fill="var(--blue)"/>
    <polygon points="441,199 926,199 926,349 534,349" fill="var(--navy)"/>
    <polygon points="536,352 926,352 926,356 538,356" fill="var(--blue)"/>

    <polygon points="0,813 926,508 926,529 0,863" fill="var(--blue)"/>
    <polygon points="0,863 926,529 926,1157 0,1157" fill="var(--navy)"/>
    <rect x="0" y="1166" width="926" height="34" fill="var(--sky)"/>

    <!-- Education -->
    <g transform="translate(131,803)">
      <circle r="84" fill="var(--ring)"/>
      <circle r="78" fill="url(#disc)"/>
      <polygon points="-58,-10 0,-36 58,-10 0,16" fill="#fff"/>
      <path d="M-34,2 L-34,24 Q0,40 34,24 L34,2 L0,18 Z" fill="#fff"/>
      <line x1="48" y1="-6" x2="48" y2="44" stroke="#fff" stroke-width="3"/>
      <rect x="44" y="40" width="8" height="14" fill="#fff"/>
    </g>
    <!-- Computer & Information Science -->
    <g transform="translate(361,747)">
      <circle r="84" fill="var(--ring)"/>
      <circle r="78" fill="url(#disc)"/>
      <rect x="-16" y="-8" width="58" height="38" rx="3" fill="none" stroke="#fff" stroke-width="5"/>
      <rect x="-26" y="34" width="78" height="6" rx="2" fill="#fff"/>
      <circle cx="-10" cy="-20" r="16" fill="none" stroke="#fff" stroke-width="8" stroke-dasharray="5 3.4"/>
      <circle cx="-10" cy="-20" r="10" fill="none" stroke="#fff" stroke-width="4"/>
      <circle cx="-38" cy="10" r="10" fill="none" stroke="#fff" stroke-width="6" stroke-dasharray="4 3"/>
      <circle cx="-38" cy="10" r="5" fill="none" stroke="#fff" stroke-width="3"/>
    </g>
    <!-- Technology & Engineering -->
    <g transform="translate(574,663)">
      <circle r="84" fill="var(--ring)"/>
      <circle r="78" fill="url(#disc)"/>
      <circle r="34" fill="none" stroke="#fff" stroke-width="14" stroke-dasharray="9 6"/>
      <circle r="24" fill="none" stroke="#fff" stroke-width="12"/>
      <ellipse cx="12" cy="0" rx="38" ry="13" fill="none" stroke="#fff" stroke-width="3" transform="rotate(60 12 0)"/>
      <ellipse cx="12" cy="0" rx="38" ry="13" fill="none" stroke="#fff" stroke-width="3" transform="rotate(-60 12 0)"/>
      <circle cx="12" cy="0" r="5" fill="#fff"/>
    </g>
    <!-- Health -->
    <g transform="translate(802,577)">
      <circle r="84" fill="var(--ring)"/>
      <circle r="78" fill="url(#disc)"/>
      <rect x="-3" y="-44" width="6" height="94" fill="#fff"/>
      <circle cx="0" cy="-44" r="7" fill="#fff"/>
      <path d="M-4,-30 Q-30,-36 -54,-24 Q-40,-18 -30,-20 Q-38,-12 -28,-10 Q-16,-10 -4,-18 Z" fill="#fff"/>
      <path d="M4,-30 Q30,-36 54,-24 Q40,-18 30,-20 Q38,-12 28,-10 Q16,-10 4,-18 Z" fill="#fff"/>
      <path d="M0,-14 C-22,-6 -22,6 0,12 C22,18 22,30 0,36 M0,-14 C22,-6 22,6 0,12 C-22,18 -22,30 0,36" fill="none" stroke="#fff" stroke-width="5"/>
    </g>
  </svg>

  <div class="abs brand brand-school"><span class="brand-mark"></span><span>Birchmont Public Schools</span></div>
  <div class="abs brand brand-college"><span class="brand-mark round"></span><span>West Haven Valley College</span></div>

  <h1 class="abs program-title">BRV Early College Program</h1>
  <p class="abs program-lede">Earn credit for both High School and College and Learn more about the career focused courses in</p>

  <section class="abs perks">
    <h2 class="perks-heading">THINGS TO LOOK FORWARD TO:</h2>
    <ul class="perks-list">
      <li><svg width="15" height="15" viewBox="0 0 15 15"><circle cx="7.5" cy="7.5" r="7.5" fill="var(--blue)"/><path d="M6 4.5 L9 7.5 L6 10.5" fill="none" stroke="#fff" stroke-width="2"/></svg>Experience college in high school</li>
      <li><svg width="15" height="15" viewBox="0 0 15 15"><circle cx="7.5" cy="7.5" r="7.5" fill="var(--blue)"/><path d="M6 4.5 L9 7.5 L6 10.5" fill="none" stroke="#fff" stroke-width="2"/></svg>Finish college early</li>
      <li><svg width="15" height="15" viewBox="0 0 15 15"><circle cx="7.5" cy="7.5" r="7.5" fill="var(--blue)"/><path d="M6 4.5 L9 7.5 L6 10.5" fill="none" stroke="#fff" stroke-width="2"/></svg>Save money on college tuition and fees</li>
      <li><svg width="15" height="15" viewBox="0 0 15 15"><circle cx="7.5" cy="7.5" r="7.5" fill="var(--blue)"/><path d="M6 4.5 L9 7.5 L6 10.5" fill="none" stroke="#fff" stroke-width="2"/></svg>Get advice on your future career</li>
    </ul>
  </section>

  <div class="abs pathway-label" style="left:131px; top:896px;">EDUCATION</div>
  <div class="abs pathway-label" style="left:361px; top:842px;">COMPUTER &amp;<br>INFORMATION SCIENCE</div>
  <div class="abs pathway-label" style="left:574px; top:758px;">TECHNOLOGY &amp;<br>ENGINEERING</div>
  <div class="abs pathway-label" style="left:802px; top:673px;">HEALTH</div>

  <div class="abs contact-banner">FOR MORE INFORMATION CONTACT</div>

  <section class="abs contact" style="left:49px;">
    <h3 class="contact-name">Gavin Purdy</h3>
    <p class="contact-line">ZT12 Alliances</p>
    <p class="contact-line">WHVC</p>
    <p class="contact-line contact-mail"><svg width="15" height="10" viewBox="0 0 15 10"><rect width="15" height="10" fill="var(--sky)"/><path d="M0 0 L7.5 6 L15 0" fill="none" stroke="var(--navy)" stroke-width="1.2"/></svg>gpurdy@whvc-example.edu</p>
  </section>
  <section class="abs contact" style="left:309px;">
    <h3 class="contact-name">Ms. Okafuji</h3>
    <p class="contact-line">Early College Coordinator</p>
    <p class="contact-line">Room J215</p>
    <p class="contact-line contact-mail"><svg width="15" height="10" viewBox="0 0 15 10"><rect width="15" height="10" fill="var(--sky)"/><path d="M0 0 L7.5 6 L15 0" fill="none" stroke="var(--navy)" stroke-width="1.2"/></svg>dena.okafuji@birchmont-example.org</p>
  </section>
  <section class="abs contact" style="left:624px;">
    <h3 class="contact-name">Ms. Varga</h3>
    <p class="contact-line">Work-Based Learning Coordinator</p>
    <p class="contact-line">Room J215</p>
    <p class="contact-line contact-mail" style="font-size:15px;"><svg width="15" height="10" viewBox="0 0 15 10"><rect width="15" height="10" fill="var(--sky)"/><path d="M0 0 L7.5 6 L15 0" fill="none" stroke="var(--navy)" stroke-width="1.2"/></svg>tessa.varga@birchmont-example.org</p>
  </section>
</main>
</body>
</html>
```